Business Card, A4 Letter Head and DL Envelope for Brandvelle

We are looking for a design for our Business Card, A4 Letter Head and DL Envelope.

Brandvelle is a distributor of promotional products. We specialize in a range of branded promotional products, these include pens, polo shirts, key rings, drink bottles, uniforms and bags to name a few. We are experts in marketing and assist companies in choosing the right promotional product for their needs. We will predominately be an online business where customers visit our website and browse our range of promotional products and branding options.

Our colours are black, red, white and grey.

Files must be supplied in eps, pdf and ai format.

Please display the following information:
Derek Halloway
Account Manager
Suite xxx, 212 Ferrow Lane Melbourne, Victoria 3000
Phone +61 3 5550 1827
Mobile +61 455 016 342
sales@brandvelle-example.com.au
www.brandvelle-example.com.au

```html
<!DOCTYPE html>
<html lang="en">
<head>
<meta charset="utf-8">
<title>Brandvelle Stationery</title>
<link href="https://fonts.googleapis.com/css2?family=Michroma&family=Roboto+Condensed:wght@400;700&display=swap" rel="stylesheet">
<style>
:root{
  --red:#c41e24;
  --red-light:#e04a4e;
  --ink:#3a3a3a;
  --grey:#555;
  --white:#fff;
  --body:"Roboto Condensed", Arial, sans-serif;
  --display:"Michroma", Arial, sans-serif;
}
*{margin:0;padding:0;box-sizing:border-box}
html,body{width:1200px;height:1000px;overflow:hidden}
body{background:var(--grey);position:relative;font-family:var(--body)}
.sheet{position:absolute;background:var(--white);overflow:hidden;box-shadow:0 2px 8px rgba(0,0,0,.35)}
.band{position:absolute;left:0;width:100%;background:linear-gradient(90deg,var(--red) 0%,var(--red) 75%,var(--red-light) 100%)}
.hook{position:absolute;overflow:visible}
.brand{position:absolute;display:flex;align-items:center;gap:8px}
.brand-dot{border-radius:50%;background:var(--red);flex:none}
.brand-name{font-family:var(--body);font-weight:700;color:var(--ink);text-transform:uppercase;letter-spacing:.5px;line-height:1}
.contacts{position:absolute;list-style:none;line-height:1.25}
.contacts li{display:flex;align-items:center;gap:4px}
.contacts svg{flex:none}
.faint-circle{position:absolute;border-radius:50%;background:radial-gradient(circle at 40% 35%,#fff 0%,#eee 55%,#ddd 100%);opacity:.8}

/* Letterhead */
.letterhead{left:87px;top:20px;width:528px;height:682px}
.letterhead .band{top:0;height:30px}
.letterhead .brand{left:34px;top:56px}
.letterhead .brand-dot{width:36px;height:36px}
.letterhead .brand-name{font-size:18px}
.letterhead .contacts{left:416px;top:56px;font-size:6.5px;color:var(--ink);border-left:1px solid var(--red);padding-left:4px}
.letterhead .contacts li:nth-child(n+3){color:var(--red)}
.letterhead .faint-circle{left:366px;top:484px;width:136px;height:136px}
.letterhead .footer{position:absolute;left:0;bottom:14px;width:100%;display:flex;align-items:center;gap:8px}
.letterhead .footer .rule{flex:1;height:6px;background:var(--red)}
.letterhead .footer .address{font-size:7px;color:var(--red);white-space:nowrap}
.letterhead .base-rule{position:absolute;left:0;bottom:6px;width:100%;height:2px;background:var(--red)}

/* Card front */
.card-front{left:663px;top:42px;width:406px;height:241px}
.card-front .band{top:0;height:176px}
.card-front .holder{position:absolute;right:26px;top:14px;text-align:left;color:var(--white)}
.card-front .holder-name{font-family:var(--display);font-size:19px;font-weight:400;letter-spacing:.5px}
.card-front .holder-role{font-size:10px;margin-top:2px}
.card-front .contacts{left:34px;top:122px;font-size:11px;color:var(--white)}
.card-front .brand{left:110px;top:190px}
.card-front .brand-dot{width:36px;height:36px}
.card-front .brand-name{font-size:18px}

/* Card back */
.card-back{left:663px;top:309px;width:406px;height:242px}
.card-back .brand{left:0;right:0;top:56px;flex-direction:column;gap:10px}
.card-back .brand-dot{width:56px;height:56px}
.card-back .brand-name{font-size:22px}
.card-back .band{top:162px;height:46px}
.card-back .details{position:absolute;left:0;top:170px;width:100%;text-align:center;color:var(--white);font-size:11px;line-height:1.5}
.card-back .details span{display:inline-flex;align-items:center;gap:4px}

/* Envelope */
.envelope{left:40px;top:712px;width:623px;height:271px}
.envelope .band{top:20px;height:22px}
.envelope .brand{left:36px;top:76px;flex-direction:column;gap:6px}
.envelope .brand-dot{width:38px;height:38px}
.envelope .brand-name{font-size:14px}
.envelope .contacts{left:40px;top:153px;font-size:7.5px;color:var(--ink);border-left:1px solid var(--red);padding-left:4px}
.envelope .return-address{position:absolute;left:36px;top:189px;font-size:7.5px;color:var(--red);line-height:1.3}
.envelope .faint-circle{left:516px;top:158px;width:66px;height:66px}
.envelope .base-rule{position:absolute;left:0;bottom:16px;width:100%;height:6px;background:var(--red)}
</style>
</head>
<body>

<!-- Letterhead -->
<section class="sheet letterhead">
  <div class="band"></div>
  <svg class="hook" style="left:96px;top:16px" width="20" height="26" viewBox="0 0 20 26"><path d="M0 14 Q12 12 14 0 Q18 12 12 14 Z" fill="#c41e24"/></svg>
  <div class="brand"><span class="brand-dot"></span><span class="brand-name">Brandvelle</span></div>
  <ul class="contacts">
    <li>+61 455 016 342</li>
    <li>+61 3 5550 1827</li>
    <li>sales@brandvelle-example.com.au</li>
    <li>www.brandvelle-example.com.au</li>
  </ul>
  <div class="faint-circle" role="img" aria-label="Faint decorative circle"></div>
  <div class="footer"><span class="rule"></span><span class="address">Suite xxx, 212 Ferrow Lane Melbourne, Victoria 3000</span><span class="rule"></span></div>
  <div class="base-rule"></div>
</section>

<!-- Business card front -->
<section class="sheet card-front">
  <div class="band"></div>
  <svg class="hook" style="left:344px;top:146px" width="22" height="34" viewBox="0 0 22 34"><path d="M0 30 Q16 26 18 0 Q24 24 14 32 Z" fill="#fff"/></svg>
  <div class="holder">
    <div class="holder-name">Derek Halloway</div>
    <div class="holder-role">Account Manager</div>
  </div>
  <ul class="contacts">
    <li><svg width="9" height="11" viewBox="0 0 9 11"><rect x="1.5" y=".5" width="6" height="10" rx="1" fill="none" stroke="#fff"/></svg>+61 455 016 342</li>
    <li><svg width="9" height="11" viewBox="0 0 9 11"><path d="M2 1 L4 3 L3 5 Q4 7 6 8 L8 7 L9 9 Q7 11 4 9 Q1 6 1 3 Z" fill="#fff"/></svg>+61 3 5550 1827</li>
    <li><svg width="9" height="11" viewBox="0 0 9 11"><rect x=".5" y="3" width="8" height="6" fill="none" stroke="#fff"/><path d="M.5 3 L4.5 6.5 L8.5 3" fill="none" stroke="#fff"/></svg>sales@brandvelle-example.com.au</li>
  </ul>
  <div class="brand"><span class="brand-dot"></span><span class="brand-name">Brandvelle</span></div>
</section>

<!-- Business card back -->
<section class="sheet card-back">
  <div class="brand"><span class="brand-dot"></span><span class="brand-name">Brandvelle</span></div>
  <div class="band"></div>
  <svg class="hook" style="left:346px;top:176px" width="22" height="34" viewBox="0 0 22 34"><path d="M0 30 Q16 26 18 0 Q24 24 14 32 Z" fill="#fff"/></svg>
  <div class="details">
    <div>Suite xxx, 212 Ferrow Lane Melbourne, Victoria 3000</div>
    <div><span><svg width="10" height="10" viewBox="0 0 10 10"><circle cx="5" cy="5" r="4.3" fill="none" stroke="#fff"/><path d="M.7 5 H9.3 M5 .7 Q2 5 5 9.3 Q8 5 5 .7" fill="none" stroke="#fff" stroke-width=".8"/></svg>www.brandvelle-example.com.au</span></div>
  </div>
</section>

<!-- DL envelope -->
<section class="sheet envelope">
  <div class="band"></div>
  <svg class="hook" style="left:110px;top:24px" width="20" height="24" viewBox="0 0 20 24"><path d="M0 20 Q12 18 14 2 Q18 16 12 20 Z" fill="#c41e24"/></svg>
  <div class="brand"><span class="brand-dot"></span><span class="brand-name">Brandvelle</span></div>
  <ul class="contacts">
    <li>+61 455 016 342</li>
    <li>+61 3 5550 1827</li>
    <li>sales@brandvelle-example.com.au</li>
    <li>www.brandvelle-example.com.au</li>
  </ul>
  <div class="return-address">Suite xxx, 212 Ferrow Lane<br>Melbourne, Victoria 3000</div>
  <div class="faint-circle" role="img" aria-label="Faint decorative circle"></div>
  <div class="base-rule"></div>
</section>

</body>
</html>
```